Personal Business Card design contest for freelance work

Include

Brenvola.net/in/DanielMWhitacre (as URL and/or QR Code)
Daniel Whitacre
(555) 218-9034
DanielMWhitacre@Pelmora.com
Houston, TX

Industry/Entity Type

Business

```html
<!DOCTYPE html>
<html lang="en">
<head>
<meta charset="utf-8">
<title>Daniel Whitacre – Business Card</title>
<link rel="stylesheet" href="https://fonts.googleapis.com/css2?family=Lato:wght@400;700&family=Arimo:wght@400&display=swap">
<style>
  :root {
    --backdrop: #2a2c2d;
    --card-front: #eef0f0;
    --card-back: #1f2222;
    --accent-blue: #3ea6ea;
    --ink: #2f3233;
    --art-tone-light: #e3e4e4;
    --art-tone-mid: #b9bcbf;
    --art-ghost: #252828;
  }
  * { margin: 0; padding: 0; box-sizing: border-box; }
  html, body { width: 1200px; height: 864px; overflow: hidden; }
  body { background: var(--backdrop); position: relative; }

  .card {
    position: absolute;
    left: 340px;
    width: 520px;
    box-shadow: 0 2px 6px rgba(0,0,0,0.45);
  }
  .card--front { top: 96px; height: 305px; background: var(--card-front); }
  .card--back  { top: 453px; height: 307px; background: var(--card-back); }

  .identity { position: absolute; left: 47px; top: 46px; }
  .identity__name {
    font-family: "Lato", sans-serif;
    font-weight: 700;
    font-size: 27px;
    line-height: 1;
    color: var(--accent-blue);
  }
  .identity__role {
    font-family: "Lato", sans-serif;
    font-weight: 400;
    font-size: 16px;
    line-height: 20px;
    color: var(--ink);
    margin-top: 3px;
  }

  .contact {
    position: absolute;
    left: 47px;
    top: 126px;
    font-family: "Arimo", Arial, sans-serif;
    font-size: 13.5px;
    line-height: 18px;
    list-style: none;
  }
  .contact__label { color: var(--accent-blue); }
  .contact__value { color: var(--ink); }

  .artwork {
    position: absolute;
    left: 380px;
    top: 40px;
    width: 96px;
    height: 222px;
    background: linear-gradient(to bottom, var(--art-tone-light), var(--art-tone-mid));
  }
  .artwork--ghost {
    left: 200px;
    top: 44px;
    width: 96px;
    height: 214px;
    background: var(--art-ghost);
  }
</style>
</head>
<body>
  <section class="card card--front">
    <header class="identity">
      <h1 class="identity__name">Daniel Whitacre</h1>
      <p class="identity__role">Managing Director</p>
    </header>
    <ul class="contact">
      <li class="contact__label">telephone</li>
      <li class="contact__value">(555) 218-9034</li>
      <li class="contact__label">email</li>
      <li class="contact__value">DanielMWhitacre@Pelmora.com</li>
      <li class="contact__label">web</li>
      <li class="contact__value">Brenvola.net/in/DanielMWhitacre</li>
      <li class="contact__label">address</li>
      <li class="contact__value">Houston, TX</li>
    </ul>
    <div class="artwork" role="img" aria-label="Illustration area: caricature of a man in a dark suit"></div>
  </section>

  <section class="card card--back">
    <div class="artwork artwork--ghost" role="img" aria-label="Illustration area: faint tone-on-tone version of the front illustration"></div>
  </section>
</body>
</html>
```